New, modern business card for growing audiology practice

We need a new business card for our audiology practice. Our logo and website have recently changed (more modern) and we want our business cards to reflect this change.
We conduct hearing tests, perform earwax removals, and fit & dispense hearing aids to our patients. We are a family owned practice in which the owner is the one who works directly with the patient. I have attached logos in various formats to use, as well as two ideas I found on this website; as well as a scanned copy of our current logo. Good luck!

Industry/Entity Type

Business

Contact Information for Business Card

Company name: Tolvera Hearing Center
Provider name: Peter Wolstenby, Au.D. F/NSB
Phone number: (802) 683-5127
Address: 837 W. Lindell Ave. Fenwick Falls, VT 05431
email: tolverahearing@postvane.com
website: tolverahearing.com

Colors
000000
aaaaaa
dbdbdb
cacaca
9bcb3c
afd23c
cadf82
b1b1b1

Requirements
Must have
• My card must include information in the "details" section. In the attached images, I found a few that I liked and I would like to model after - "brisky bouncin'" and "Sound Method Center".
• Must be horizontal.
• Must include logos provided. I uploaded them in various file formats and various ways.
• Must match logo font, if possible, if not, please get as close as you can.
Nice to have
• I really like the idea of having a color on one side with just the logo and company name and the contact information and provider name on the other side. I also really like the idea of having the main color dominating on the logo/company side with accent of that same color on the contact side of the card.
Should not have
• Must not be vertical.

```html
<!DOCTYPE html>
<html lang="en">
<head>
<meta charset="utf-8">
<title>Tolvera Hearing Center – Business Card</title>
<link rel="stylesheet" href="https://fonts.googleapis.com/css2?family=Roboto:wght@400;500&family=Roboto+Condensed:wght@700&display=swap">
<style>
  :root {
    --backdrop: #ece8e2;
    --card-black: #1b1c1e;
    --card-white: #f1f1f1;
    --brand-green: #739f37;
    --ink-dark: #1a1a1a;
    --ink-light: #ffffff;
  }
  * { margin: 0; padding: 0; box-sizing: border-box; }
  html, body {
    width: 1200px;
    height: 960px;
    overflow: hidden;
    background: var(--backdrop);
    font-family: "Roboto", Arial, sans-serif;
  }
  .canvas { position: relative; width: 1200px; height: 960px; }

  .card {
    position: absolute;
    left: 320px;
    width: 600px;
    border-radius: 20px;
    overflow: hidden;
  }

  /* Front side */
  .card-front {
    top: 100px;
    height: 360px;
    background: var(--card-black);
  }
  .front-brand {
    position: absolute;
    left: 0; right: 0; top: 160px;
    display: flex;
    align-items: center;
    justify-content: center;
    gap: 14px;
    color: var(--brand-green);
    font-size: 30px;
    font-weight: 500;
    letter-spacing: 2px;
    text-transform: uppercase;
  }
  .brand-dot {
    width: 22px; height: 22px;
    border-radius: 50%;
    background: var(--brand-green);
    flex: none;
  }
  .front-web {
    position: absolute;
    left: 0; right: 0; top: 301px;
    text-align: center;
    color: var(--ink-light);
    font-size: 14px;
    letter-spacing: 4.2px;
  }

  /* Back side */
  .card-back {
    top: 493px;
    height: 342px;
  }
  .back-shapes { position: absolute; inset: 0; }
  .back-brand {
    position: absolute;
    left: 34px; top: 41px;
    display: flex;
    align-items: center;
    gap: 9px;
    color: var(--ink-dark);
    font-size: 18px;
    letter-spacing: 0.7px;
    text-transform: uppercase;
  }
  .back-brand .brand-dot { width: 13px; height: 13px; }
  .provider {
    position: absolute;
    right: 30px; top: 36px;
    text-align: right;
    color: var(--ink-light);
  }
  .provider-name {
    font-family: "Roboto Condensed", "Arial Narrow", sans-serif;
    font-size: 21px;
    font-weight: 700;
    text-transform: uppercase;
  }
  .provider-title { font-size: 14px; font-weight: 500; margin-top: 3px; }
  .address {
    position: absolute;
    right: 30px; top: 208px;
    text-align: right;
    color: var(--ink-light);
    font-size: 14px;
    font-style: normal;
    line-height: 19px;
  }
  .contact-list {
    position: absolute;
    right: 30px; top: 255px;
    list-style: none;
    color: var(--ink-light);
    font-size: 14px;
    line-height: 19px;
  }
  .contact-list li {
    display: flex;
    justify-content: flex-end;
    align-items: center;
    gap: 13px;
  }
  .contact-icon { width: 13px; height: 13px; fill: var(--ink-light); flex: none; }
</style>
</head>
<body>
<main class="canvas">

  <section class="card card-front" aria-label="Card front">
    <div class="front-brand"><span class="brand-dot"></span>Tolvera Hearing Center</div>
    <p class="front-web">www.tolverahearing.com</p>
  </section>

  <section class="card card-back" aria-label="Card back">
    <svg class="back-shapes" viewBox="0 0 600 342" preserveAspectRatio="none">
      <rect width="600" height="342" fill="var(--brand-green)"/>
      <path d="M0,0 L320,0 C412,72 396,226 152,342 L0,342 Z" fill="#000"/>
      <path d="M320,0 C412,72 396,226 152,342" fill="none" stroke="#fff" stroke-width="1.5"/>
      <path d="M0,0 L316,0 C392,64 372,208 140,342 L0,342 Z" fill="var(--card-white)"/>
      <path d="M316,0 C392,64 372,208 140,342" fill="none" stroke="#fff" stroke-width="1.5"/>
    </svg>

    <div class="back-brand"><span class="brand-dot"></span>Tolvera Hearing Center</div>

    <div class="provider">
      <p class="provider-name">Peter Wolstenby</p>
      <p class="provider-title">AU.D. F/NSB</p>
    </div>

    <address class="address">
      837 W. Lindell Ave.<br>
      Fenwick Falls, VT 05431
    </address>

    <ul class="contact-list">
      <li>(802) 683-5127
        <svg class="contact-icon" viewBox="0 0 24 24" aria-hidden="true"><path d="M6.6 10.8a15.2 15.2 0 0 0 6.6 6.6l2.2-2.2c.3-.3.7-.4 1-.2 1.1.4 2.3.6 3.6.6.6 0 1 .4 1 1V20c0 .6-.4 1-1 1A17 17 0 0 1 3 4c0-.6.4-1 1-1h3.5c.6 0 1 .4 1 1 0 1.3.2 2.5.6 3.6.1.3 0 .7-.2 1z"/></svg>
      </li>
      <li>tolverahearing@postvane.com
        <svg class="contact-icon" viewBox="0 0 24 24" aria-hidden="true"><path d="M2 5h20v14H2z M3.5 6.5 12 13l8.5-6.5" fill="var(--ink-light)" stroke="var(--brand-green)" stroke-width="1.6"/></svg>
      </li>
      <li>tolverahearing.com
        <svg class="contact-icon" viewBox="0 0 24 24" aria-hidden="true"><circle cx="12" cy="12" r="10"/><path d="M2 12h20M12 2c3 3 3 17 0 20M12 2c-3 3-3 17 0 20" fill="none" stroke="var(--brand-green)" stroke-width="1.5"/></svg>
      </li>
    </ul>
  </section>

</main>
</body>
</html>
```